real esate business card with company logo and name

we need a business card design for a real esate company

The company name is Walsh & Brand Pty Ltd, and we have our logo designed and will upload. We want classic or moden feel. Black or white background. looks more textured. Should include folowinginformations
Owen Walsh and Lucy Brand
Sales Agents & Onsite Manager
p: 07 5948 2063
F: 07 5948 2174
M:0431 857 219
3/42 Marlow Crescent, FERNLEA QLD 4213

We want this business card looks professonal. Thank you in advance.

Industry/Entity Type

Real Estate Agent

Contact Information for Business Card

Owen Walsh and Lucy Brand
Onsite Manager & Sales Agents
p: 07 5948 2063
M:0431 857 219

Font styles to use
Serif

Colors
000000
fbfbfb
333333
959595

Requirements
Must have
• company logo and name, black or white back ground

```html
<!DOCTYPE html>
<html lang="en">
<head>
<meta charset="utf-8">
<title>Walsh &amp; Brand Pty Ltd — Business Card</title>
<link rel="stylesheet" href="https://fonts.googleapis.com/css2?family=Alegreya+Sans:wght@500;700&family=Open+Sans:wght@700&display=swap">
<style>
  :root {
    --ink: #000000;
    --paper: #fbfbfb;
    --charcoal: #333333;
    --mid-grey: #959595;
    --label-grey: #555555;
    --soft-grey: #4a4a4a;
    --band-text: #5a5a5a;
  }
  html, body {
    margin: 0;
    padding: 0;
    width: 1200px;
    height: 686px;
    overflow: hidden;
    background: var(--ink);
  }
  .card {
    position: relative;
    width: 1200px;
    height: 686px;
    overflow: hidden;
    background:
      radial-gradient(ellipse 520px 480px at 880px 330px, rgba(80,80,80,0.55), rgba(40,40,40,0.25) 55%, rgba(0,0,0,0) 100%),
      var(--ink);
    font-family: "Alegreya Sans", "Optima", sans-serif;
  }
  .edge-rule {
    position: absolute;
    left: 14px;
    top: 0;
    width: 5px;
    height: 686px;
    background: var(--paper);
  }
  .brand-mark {
    position: absolute;
    left: 170px;
    top: 130px;
    width: 250px;
    height: 250px;
  }
  .brand-band {
    position: absolute;
    left: 19px;
    top: 427px;
    width: 538px;
    height: 58px;
    background: var(--paper);
    display: flex;
    align-items: center;
    justify-content: center;
  }
  .brand-name {
    margin: 0;
    font-family: "Alegreya Sans", "Optima", sans-serif;
    font-weight: 500;
    font-size: 31px;
    letter-spacing: 1.5px;
    color: var(--band-text);
    text-transform: uppercase;
  }
  .agents {
    position: absolute;
    left: 552px;
    top: 84px;
    width: 600px;
    text-align: center;
  }
  .agents-names {
    margin: 0;
    font-weight: 700;
    font-size: 40px;
    line-height: 1;
    color: var(--paper);
  }
  .agents-role {
    margin: 8px 0 0;
    font-family: "Open Sans", sans-serif;
    font-weight: 700;
    font-size: 23px;
    color: var(--soft-grey);
  }
  .contact {
    position: absolute;
    right: 65px;
    top: 424px;
    margin: 0;
    padding: 0;
    list-style: none;
    text-align: right;
    font-weight: 700;
    font-size: 36px;
    line-height: 50px;
    color: var(--paper);
  }
  .contact-label {
    color: var(--label-grey);
    margin-right: 12px;
  }
  .contact-label.address {
    margin-right: 4px;
  }
</style>
</head>
<body>
  <main class="card">
    <div class="edge-rule"></div>

    <svg class="brand-mark" viewBox="0 0 250 250" aria-hidden="true">
      <rect x="30" y="30" width="190" height="190" fill="none" stroke="var(--mid-grey)" stroke-width="18"/>
    </svg>

    <div class="brand-band">
      <p class="brand-name">Walsh &amp; Brand Pty Ltd.</p>
    </div>

    <header class="agents">
      <h1 class="agents-names">Owen Walsh and Lucy Brand</h1>
      <p class="agents-role">Onsite Manager &amp; Sales Agents</p>
    </header>

    <ul class="contact">
      <li><span class="contact-label">P</span>07 5948 2063</li>
      <li><span class="contact-label">M</span>0431 857 219</li>
      <li><span class="contact-label address">A</span>3/42 Marlow Crescent</li>
      <li>FERNLEA QLD 4213</li>
    </ul>
  </main>
</body>
</html>
```